The Harbourlight Aid Trust needs a graphic of their innovation approach

What we need?
- we have designed a new innovation approach (see attached). An innovation approach is the process one goes through in order to design and launch a new product or service.
- This new graphic will be used in meetings to help others understand what innovation is and how we do it. It will also be used in training sessions and be the starting point for innovation training materials we are creating
- We have created this draft graphic by copying and pasting new words over another charities innovation process
- We would like you to use your design magic and create our very own innovation process graphic. We would like it to be neat, simple, non fussy, easy to understand /read and in line with our brand colours
Attached:
1. PowerPoint:
- Slide 1: our innovation process
- Slide 2 explanation of process to bring it to life
- Slide 3&4: brand colours
- Slide 5: inspiration / examples of other processes we like the look of
2. Typeface brand guidelines
We can't wait to see what you come up with! Thank you :)
Target Market(s)
internal employees
Industry/Entity Type
Charity
Colors
Designer to choose colors to be used in the design.
Look and feel
Each slider illustrates characteristics of the customer's brand and the style your logo design should communicate.

```html
<!DOCTYPE html>
<html lang="en">
<head>
<meta charset="utf-8">
<title>Harbourlight Aid Trust – Innovation Approach</title>
<link href="https://fonts.googleapis.com/css2?family=Arimo:wght@400;700&display=swap" rel="stylesheet">
<style>
  :root {
    --discover: #f25a5a;
    --define: #f9bd47;
    --deliver: #5bc5c4;
    --ink: #1d1d1f;
    --paper: #ffffff;
  }
  html, body { margin: 0; padding: 0; overflow: hidden; background: var(--paper); }
  .canvas { width: 1200px; height: 1094px; position: relative; }
  .process-map { display: block; width: 1200px; height: 1094px; font-family: "Arimo", Arial, sans-serif; }
  .flow { fill: none; stroke-width: 31; }
  .flow-discover { stroke: var(--discover); }
  .flow-define { stroke: var(--define); }
  .flow-deliver { stroke: var(--deliver); }
  .head-discover { fill: var(--discover); }
  .head-define { fill: var(--define); }
  .head-deliver { fill: var(--deliver); }
  .loop { fill: none; stroke-width: 2; stroke-dasharray: 7 5; }
  .loop-discover { stroke: var(--discover); }
  .loop-define { stroke: var(--define); }
  .loop-deliver { stroke: var(--deliver); }
  .node { fill: var(--paper); stroke-width: 10; }
  .node-discover { stroke: var(--discover); }
  .node-define { stroke: var(--define); }
  .node-deliver { stroke: var(--deliver); }
  .node-shadow { filter: drop-shadow(0 2px 3px rgba(0,0,0,.35)); }
  .node-label { fill: var(--ink); font-size: 17px; text-anchor: middle; }
  .step-label { fill: var(--paper); font-size: 17px; font-weight: 700; text-anchor: middle; }
  .loop-label { font-size: 18px; text-anchor: middle; }
  .phase-title { font-size: 32px; font-weight: 700; text-anchor: middle; }
  .tone-discover { fill: var(--discover); }
  .tone-define { fill: var(--define); }
  .tone-deliver { fill: var(--deliver); }
  .icon-line { fill: none; stroke-width: 3.5; stroke-linecap: round; stroke-linejoin: round; }
</style>
</head>
<body>
<main class="canvas">
<svg class="process-map" viewBox="0 0 1200 1094" xmlns="http://www.w3.org/2000/svg" aria-label="Innovation approach: Discover, Define, Deliver">

  <!-- Discover flows -->
  <path class="flow flow-discover" d="M355 345 V215 A60 60 0 0 1 415 155 H570"/>
  <polygon class="head-discover" points="567,123 600,152 567,183"/>
  <path class="flow flow-discover" d="M661 232 V355 A45 45 0 0 0 674.2 386.8"/>

  <!-- Define flows -->
  <path class="flow flow-define" d="M674.2 386.8 A45 45 0 0 0 706 400 H816"/>
  <polygon class="head-define" points="813,370 846,400 813,430"/>
  <path class="flow flow-define" d="M911 475 V665 A43 43 0 0 1 868 708 H745"/>
  <polygon class="head-define" points="748,678 716,708 748,738"/>

  <!-- Deliver flows -->
  <path class="flow flow-deliver" d="M660 782 V912 A43 43 0 0 1 617 955 H442"/>
  <polygon class="head-deliver" points="445,925 413,955 445,985"/>
  <path class="flow flow-deliver" d="M354 880 V692"/>
  <polygon class="head-deliver" points="324,695 354,662 384,695"/>

  <!-- Iteration loops -->
  <path class="loop loop-discover" d="M591 119 H358 A45 45 0 0 0 313 164 V338"/>
  <polygon class="head-discover" points="303,336 323,336 313,346"/>
  <text class="loop-label tone-discover" x="474" y="106">Interate</text>

  <path class="loop loop-define" d="M845 361 H702 V232"/>
  <polygon class="head-discover" points="692,232 712,232 702,222"/>
  <text class="loop-label tone-define" x="753" y="342">Interate</text>

  <path class="loop loop-define" d="M729 749 H905 A45 45 0 0 0 950 704 V480"/>
  <polygon class="head-define" points="939,482 961,482 950,470"/>
  <text class="loop-label tone-define" x="827" y="774">Interate</text>

  <path class="loop loop-deliver" d="M423 993 H655 A45 45 0 0 0 700 948 V786"/>
  <polygon class="head-deliver" points="689,788 711,788 700,776"/>
  <text class="loop-label tone-deliver" x="562" y="1015">Continuous Improvement</text>

  <!-- Step labels -->
  <text class="step-label" x="486" y="161">Insight</text>
  <text class="step-label" transform="translate(668 303) rotate(-90)">Ideate</text>
  <text class="step-label" x="741" y="406">(In)validate</text>
  <text class="step-label" x="807" y="716">Test</text>
  <text class="step-label" x="542" y="961">Delivery Plan</text>

  <!-- Phase titles -->
  <text class="phase-title tone-discover" x="508" y="287">Discover</text>
  <text class="phase-title tone-define" x="782" y="569">Define</text>
  <text class="phase-title tone-deliver" x="506" y="833">Deliver</text>

  <!-- Challenge -->
  <g class="node-group">
    <circle class="node node-discover node-shadow" cx="355" cy="415" r="73"/>
    <g class="icon-line" stroke="var(--discover)">
      <path d="M388 390 A36 36 0 1 1 377 369"/>
      <path d="M376 395 A24 24 0 1 1 368 380"/>
      <path d="M364 399 A12 12 0 1 1 360 390"/>
      <path d="M352 394 L390 360"/>
      <path d="M384 356 L393 348 L398 352 L390 362"/>
    </g>
    <text class="node-label" x="355" y="454">Challenge</text>
  </g>

  <!-- Opportunity Statement -->
  <g class="node-group">
    <circle class="node node-discover" cx="661" cy="156" r="73"/>
    <g class="icon-line" stroke="var(--discover)" stroke-width="4">
      <path d="M661 152 V98"/>
      <path d="M661 134 Q661 126 645 118 L631 108"/>
      <path d="M661 134 Q661 126 677 118 L691 108"/>
      <path d="M654 104 L661 94 L668 104"/>
      <path d="M630 116 L627 106 L638 105"/>
      <path d="M692 116 L695 106 L684 105"/>
    </g>
    <text class="node-label" x="661" y="176">Opportunity</text>
    <text class="node-label" x="661" y="198">Statement</text>
  </g>

  <!-- Concepts -->
  <g class="node-group">
    <circle class="node node-define" cx="911" cy="402" r="73"/>
    <g class="icon-line" stroke="var(--define)" stroke-width="2.5">
      <path d="M900 400 Q890 390 890 375 A21 21 0 0 1 932 375 Q932 390 922 400 V408 H900 Z"/>
      <path d="M902 413 H920 M904 418 H918"/>
      <circle cx="911" cy="372" r="5"/>
      <circle cx="912" cy="390" r="5"/>
      <path d="M896 344 L893 337 M926 344 L929 337 M880 366 L866 363 M942 366 L956 363 M885 395 L875 402 M937 395 L947 402"/>
    </g>
    <text class="node-label" x="911" y="440">Concepts</text>
  </g>

  <!-- Solution -->
  <g class="node-group">
    <circle class="node node-deliver" cx="659" cy="708" r="73"/>
    <g class="tone-deliver">
      <rect x="623" y="653" width="38" height="38"/>
      <rect x="664" y="653" width="32" height="38"/>
      <rect x="623" y="694" width="38" height="31"/>
      <rect x="664" y="698" width="47" height="39"/>
      <circle cx="661" cy="680" r="5" fill="var(--paper)"/>
      <circle cx="677" cy="686" r="5"/>
      <circle cx="651" cy="708" r="5" fill="var(--paper)"/>
      <circle cx="693" cy="697" r="5"/>
    </g>
    <text class="node-label" x="659" y="755">Solution</text>
  </g>

  <!-- Launch -->
  <g class="node-group">
    <circle class="node node-deliver" cx="354" cy="955" r="73"/>
    <g class="tone-deliver">
      <path d="M355 890 Q370 902 370 918 L368 950 L374 956 V966 L366 962 H344 L336 966 V956 L342 950 L340 918 Q340 902 355 890 Z"/>
      <circle cx="355" cy="917" r="7" fill="var(--paper)"/>
      <circle cx="355" cy="934" r="4" fill="var(--paper)"/>
    </g>
    <path class="icon-line" stroke="var(--deliver)" stroke-width="2" d="M347 969 V982 M355 969 V982 M363 969 V982"/>
    <text class="node-label" x="354" y="1006">Launch</text>
  </g>
</svg>
</main>
</body>
</html>
```